Business Card Design

I already have a company logo for my company. I have a logo for the manufacturer we represent. I want a professional business card design.

```html
<!DOCTYPE html>
<html lang="en">
<head>
<meta charset="utf-8">
<title>Beacon Alert Systems – Business Card</title>
<link rel="stylesheet" href="https://fonts.googleapis.com/css2?family=Open+Sans:wght@400;600;700;800&display=swap">
<style>
  :root{
    --stage:#222223;
    --card-black:#1c1c1f;
    --brand-red:#e31e24;
    --brand-red-deep:#d81c22;
    --brand-orange:#ee6a2c;
    --brand-gold:#b8902a;
    --ink-white:#ffffff;
    --ink-soft:#f1f1f1;
  }
  *{box-sizing:border-box;margin:0;padding:0}
  html,body{width:1200px;height:780px;overflow:hidden;background:var(--stage)}
  body{font-family:"Open Sans",Arial,sans-serif;position:relative}

  .card{position:absolute;top:236px;width:540px;height:309px;border-radius:24px;overflow:hidden}
  .card--front{left:40px;background:var(--card-black)}
  .card--back{left:620px;background:var(--brand-red)}

  /* front: brand name */
  .brand{position:absolute;left:0;right:0;top:52px;display:flex;align-items:center;justify-content:center;gap:14px}
  .brand__dot{width:30px;height:30px;border-radius:50%;background:var(--brand-red)}
  .brand__name{font-weight:800;font-size:30px;line-height:1;color:var(--ink-white);letter-spacing:1px;text-transform:uppercase}

  /* front: info band */
  .band{position:absolute;left:0;top:148px;width:540px;height:92px}
  .band svg{position:absolute;inset:0}
  .identity{position:absolute;left:22px;top:14px}
  .identity__name{font-weight:700;font-size:25px;line-height:1.1;color:var(--ink-white)}
  .identity__first{color:var(--brand-red)}
  .identity__title{font-size:15px;color:var(--ink-white);margin-top:4px}
  .band__mark{position:absolute;left:236px;top:22px;width:48px;height:48px;border-radius:50%;background:var(--card-black);border:3px solid var(--ink-soft)}

  .contacts{position:absolute;left:306px;top:10px;list-style:none}
  .contacts li{display:flex;align-items:center;gap:8px;font-size:14.5px;line-height:24px;color:var(--ink-white)}
  .contacts svg{position:static;width:14px;height:14px;flex:none}

  .address{position:absolute;left:22px;top:258px;font-size:14.5px;color:var(--ink-soft)}

  /* back */
  .back__pattern{position:absolute;inset:0;background:linear-gradient(115deg,var(--brand-red-deep) 0%,var(--brand-red) 45%,var(--brand-orange) 100%)}
  .back__brand{position:absolute;right:26px;bottom:22px;display:flex;align-items:center;gap:6px}
  .back__dot{width:12px;height:12px;border-radius:50%;background:var(--ink-white)}
  .back__name{font-weight:700;font-size:10px;color:var(--ink-white);text-transform:uppercase;letter-spacing:.5px}
</style>
</head>
<body>

<section class="card card--front" aria-label="Business card front">
  <div class="brand">
    <span class="brand__dot"></span>
    <span class="brand__name">Beacon Alert Systems</span>
  </div>

  <div class="band">
    <svg width="540" height="92" viewBox="0 0 540 92" aria-hidden="true">
      <polygon points="0,0 262,0 232,92 0,92" fill="var(--brand-gold)"/>
      <polygon points="262,0 540,0 540,92 232,92" fill="var(--brand-red)"/>
    </svg>
    <div class="identity">
      <p class="identity__name"><span class="identity__first">Lena</span> Marvik</p>
      <p class="identity__title">Managing Director</p>
    </div>
    <span class="band__mark"></span>
    <ul class="contacts">
      <li>
        <svg viewBox="0 0 24 24" aria-hidden="true"><path fill="#fff" d="M6.6 10.8a15 15 0 0 0 6.6 6.6l2.2-2.2c.3-.3.7-.4 1-.2 1.1.4 2.3.6 3.6.6.6 0 1 .4 1 1V20c0 .6-.4 1-1 1C10.6 21 3 13.4 3 4c0-.6.4-1 1-1h3.5c.6 0 1 .4 1 1 0 1.3.2 2.5.6 3.6.1.3 0 .7-.2 1z"/></svg>
        (555) 014-2276
      </li>
      <li>
        <svg viewBox="0 0 24 24" aria-hidden="true"><rect x="2" y="5" width="20" height="14" rx="2" fill="#fff"/><path d="M3 6l9 7 9-7" fill="none" stroke="#e31e24" stroke-width="2"/></svg>
        hello@beaconalert.com
      </li>
      <li>
        <svg viewBox="0 0 24 24" aria-hidden="true"><circle cx="12" cy="12" r="10" fill="#fff"/><path d="M2 12h20M12 2c3 3 3 17 0 20M12 2c-3 3-3 17 0 20" fill="none" stroke="#e31e24" stroke-width="1.6"/></svg>
        www.beaconalert.com
      </li>
    </ul>
  </div>

  <p class="address">4180 Harbor View Ct #210, Melbourne, FL 32901, USA</p>
</section>

<section class="card card--back" aria-label="Business card back">
  <div class="back__pattern" role="img" aria-label="Repeating brand pattern in red and orange"></div>
  <div class="back__brand">
    <span class="back__dot"></span>
    <span class="back__name">Beacon Alert Systems</span>
  </div>
</section>

</body>
</html>
```